We want to revamp our current website -www.kelvota-eng.com

We need to have a new website for our company that offers non-destructive and testing solutions around Africa. We have a current website but it does not fulfil our needs as it is:<br/>1. Not clear and bright<br/>2. Does not fit well in mobile <br/>3. Is not easily updatable by our staff. <br/>4. Is not linked to our social media sites.<br/>We would like to have a website that addresses the above issues. Our colours are Red and Blue and should communicate to our clients, that we are a professional company open for business, ready to solve their non-destructive testing problems around Africa. * Helpful if it is a wordpress website.

Target Market(s)

Our customers are B2B Corporate clients. We mainly work in
1. Storage Terminals
2. Refineries
3. Oil and Gas offshore and onshore rigs.

Industry/Entity Type

Oil And Gas

Contact Information for Business Card

Please find our current business card on the uploaded files.

Coding

Coded - Design and coding required

Number of Pages Required

5+ page

Font styles to use
Serif
Sans Serif

Requirements
Must have
• I like this site www.pirelo-inspection.com They are in the same industry.
• I don't understand how to call them but all the 'call to action' buttons, and links to our Social media pages.
• Must have a place where we update information in a regular basis. A Blog!

```html
<!DOCTYPE html>
<html lang="en">
<head>
<meta charset="utf-8">
<title>Kelvota Engineering</title>
<link rel="stylesheet" href="https://fonts.googleapis.com/css2?family=Montserrat:wght@500;600;700&family=Questrial&display=swap">
<style>
:root{
  --red:#b3151c;
  --red-dark:#8e0f15;
  --blue:#213479;
  --blue-dark:#16235a;
  --ink:#222;
  --muted:#8a8a8a;
  --light:#f0eff1;
  --footer:#555353;
  --white:#fff;
}
*{margin:0;padding:0;box-sizing:border-box}
html,body{width:1200px;height:4389px;overflow:hidden}
body{position:relative;background:var(--white);font-family:"Questrial",sans-serif;color:var(--ink)}
.abs{position:absolute}
h1,h2,h3,h4,.head{font-family:"Montserrat",sans-serif}
.title{position:absolute;left:0;width:1200px;text-align:center;font-size:31px;font-weight:700;color:var(--red)}
.title span{color:var(--blue)}
.lead{position:absolute;left:300px;width:600px;text-align:center;font-size:14px;line-height:27px;color:#333}

/* header */
.site-header{position:absolute;left:0;top:0;width:1200px;height:94px;background:var(--white)}
.brand{position:absolute;left:111px;top:10px;display:flex;align-items:center;gap:12px}
.brand-dot{width:95px;height:80px;border-radius:50%;background:var(--blue);border:4px solid var(--red)}
.brand-name{font-family:"Montserrat",sans-serif;font-weight:700;font-size:15px;color:var(--red)}
.nav{position:absolute;top:38px;font-size:12.5px;color:#333;letter-spacing:.2px}
.nav.active{color:var(--red)}
.nav.active::after{content:"";position:absolute;left:0;right:0;top:25px;height:2px;background:var(--red)}

/* hero */
.hero{position:absolute;left:0;top:94px;width:1200px;height:656px;
  background:linear-gradient(180deg,#4d5a6c 0%,#33404f 40%,#263140 70%,#3a4654 100%);
  clip-path:polygon(0 0,100% 0,100% 78%,50% 100%,0 84%)}
.hero h1{position:absolute;top:200px;left:0;width:1200px;text-align:center;color:var(--white);font-size:52px;font-weight:700;letter-spacing:1px}
.hero h2{position:absolute;top:273px;left:0;width:1200px;text-align:center;color:var(--white);font-size:18px;font-weight:500}
.hero p{position:absolute;top:308px;left:220px;width:760px;text-align:center;color:var(--white);font-size:15px;line-height:34px}
.btn{position:absolute;display:flex;align-items:center;justify-content:center;font-family:"Montserrat",sans-serif;font-weight:600;color:var(--white);font-size:14px}
.btn-hero{left:522px;top:398px;width:160px;height:46px;background:var(--red-dark);clip-path:polygon(0 0,92% 0,100% 100%,8% 100%)}
.hero-arrow{position:absolute;top:310px;width:44px;height:44px;border:2px solid rgba(255,255,255,.8);border-radius:50%}

/* about */
.about{position:absolute;left:0;top:750px;width:1200px;height:699px;background:var(--light)}
.about h2{position:absolute;left:111px;font-size:30px;font-weight:700;color:var(--red)}
.about h3{position:absolute;left:111px;font-size:24px;font-weight:600;color:#111}
.about .kicker{position:absolute;left:111px;top:148px;font-size:13px;font-weight:600;font-family:"Montserrat",sans-serif}
.about p{position:absolute;left:111px;width:490px;font-size:14px;line-height:34.5px;color:var(--muted);text-align:justify}
.value{position:absolute;top:490px;width:120px;text-align:center;font-size:13px;line-height:19px;color:#333}
.value i{display:block;margin:0 auto 8px;width:68px;height:68px;border-radius:50%;background:var(--white);border:2px solid #e3dfe4}
.frame{position:absolute;left:653px;top:124px;width:390px;height:418px;border:2px solid var(--blue);border-top-color:var(--blue);border-right-color:var(--red)}
.frame::before{content:"";position:absolute;left:-2px;top:-2px;width:195px;height:2px;background:var(--blue)}
.frame::after{content:"";position:absolute;right:-2px;top:-2px;width:195px;height:2px;background:var(--red)}
.about-photo{position:absolute;left:682px;top:170px;width:409px;height:415px;background:linear-gradient(160deg,#8c8f96 0%,#c17a3c 40%,#3a5ea8 60%,#6b5a45 100%);box-shadow:0 4px 14px rgba(0,0,0,.15)}

/* focus */
.card{position:absolute;color:var(--white)}
.card .num{position:absolute;left:32px;font-family:"Montserrat",sans-serif;font-size:30px;font-weight:700}
.card .label{position:absolute;left:32px;font-family:"Montserrat",sans-serif;font-size:15px;font-weight:500;line-height:22px}
.card .text{position:absolute;left:18px;width:350px;font-size:13.5px;line-height:24px;text-align:justify}
.link{position:absolute;font-family:"Montserrat",sans-serif;font-size:14px;font-weight:600;color:var(--white);text-decoration:underline}

/* how it works */
.how{position:absolute;left:0;top:2117px;width:1200px;height:419px;background:linear-gradient(100deg,#0c1222 0%,#1f3a6e 40%,#2c5a9e 70%,#173056 100%)}
.how h2{position:absolute;top:128px;left:0;width:1200px;text-align:center;color:var(--white);font-size:31px;font-weight:700}

/* blogs */
.blog{position:absolute;top:2765px;width:317px;height:254px;color:var(--white)}
.blog .meta{position:absolute;left:17px;font-family:"Montserrat",sans-serif;font-size:13px;line-height:24px}
.carousel-arrow{position:absolute;top:2880px;font-size:26px;color:#555}

/* services */
.svc{position:absolute;top:3116px;width:600px;height:450px;color:var(--white)}
.svc h3{position:absolute;top:52px;font-size:20px;font-weight:600;letter-spacing:.3px}
.svc p{position:absolute;top:100px;width:470px;font-size:14.5px;line-height:29px}
.svc ul{position:absolute;top:192px;list-style:none;font-family:"Montserrat",sans-serif;font-size:14.5px;line-height:32px}
.svc li::before{content:"»";margin-right:12px}
.btn-svc{top:388px;width:182px;height:52px;clip-path:polygon(0 0,88% 0,100% 100%,12% 100%)}
.svc-badge{position:absolute;left:515px;top:3289px;width:170px;height:112px;border-radius:50%;background:var(--white);display:flex;align-items:center;justify-content:center;font-family:"Montserrat",sans-serif;font-weight:700;font-size:17px;color:var(--blue);box-shadow:0 0 0 6px rgba(255,255,255,.25)}

/* clients */
.client{position:absolute;top:3718px;width:235px;height:102px;background:var(--white);border:1px solid #e7e7e7;box-shadow:0 2px 8px rgba(0,0,0,.08);display:flex;align-items:center;justify-content:center;gap:10px;font-family:"Montserrat",sans-serif;font-weight:600;font-size:17px;color:var(--blue)}
.client i{width:14px;height:14px;border-radius:50%;background:var(--red)}
.dots{position:absolute;top:3848px;left:564px;display:flex;gap:9px}
.dots b{width:10px;height:10px;border-radius:50%;background:#444}
.dots b.on{background:var(--red-dark)}

/* footer */
.site-footer{position:absolute;left:0;top:3955px;width:1200px;height:434px;background:linear-gradient(180deg,#5d5b5b,#4b4949);color:#ddd}
.site-footer h4{position:absolute;font-size:14px;font-weight:600;color:var(--white)}
.site-footer .col{position:absolute;font-size:13px;line-height:28px}
.contact-row{display:flex;gap:18px;align-items:flex-start;margin-bottom:14px;line-height:22px}
.contact-row svg{flex:none;margin-top:4px}
.email{position:absolute;left:844px;top:4070px;width:172px;height:43px;background:var(--white);color:#999;font-size:13px;padding:13px 16px}
.send{position:absolute;left:1016px;top:4070px;width:72px;height:43px;background:var(--blue);display:flex;align-items:center;justify-content:center}
.social{position:absolute;top:4150px;width:14px;height:14px;border-radius:50%;border:1.5px solid #ccc}
.copyright{position:absolute;left:0;top:4322px;width:1200px;text-align:center;font-size:14px;color:#eee}
.footer-rule{position:absolute;left:111px;top:4292px;width:976px;height:1px;background:rgba(255,255,255,.12)}
</style>
</head>
<body>

<header class="site-header">
  <div class="brand"><div class="brand-dot"></div><span class="brand-name">KELVOTA ENGINEERING</span></div>
  <span class="nav active" style="left:506px">HOME</span>
  <span class="nav" style="left:571px">ABOUT US</span>
  <span class="nav" style="left:660px">INSPECTION</span>
  <span class="nav" style="left:760px">ENGINEERING SERVICES</span>
  <span class="nav" style="left:928px">CONTACT US</span>
  <span class="nav" style="left:1038px">MORE ⌄</span>
</header>

<section class="hero" role="img" aria-label="Night view of an illuminated oil refinery and storage tanks">
  <h1>KELVOTA ENGINEERING</h1>
  <h2>WE OFFER INSPECTION &amp; ENGINEERING SERVICES</h2>
  <p>With roots in Coastline City, we have over 15 years' experience in NDT, Mechanical engineering and Marine services. We enjoy a regional presence in The larger Eastern and Central African Region</p>
  <a class="btn btn-hero">GET STARTED</a>
  <span class="hero-arrow" style="left:65px"></span>
  <span class="hero-arrow" style="left:1088px"></span>
</section>

<section class="about">
  <h2 style="top:98px">ABOUT US</h2>
  <div class="kicker">HERE'S A SYNOPSIS ABOUT US.</div>
  <p style="top:176px">Our operations are split into two divisions, Kelvota Inspection Services and Kelvota Engineering services.<br>We pick the best talent from the industry and have heavily invested in our developing our staff skills further through regular rigorous external and internal training to keep up with the industry trends.</p>
  <h3 style="top:366px">OUR VALUES</h3>
  <p style="top:405px">Respect and diversity, ethics and integrity, safety and sustainability are important elements of our values.</p>
  <div class="value" style="left:103px"><i></i>PASSION FOR<br>INNOVATIO</div>
  <div class="value" style="left:298px"><i></i>CUSTOMER<br>OBSESSION</div>
  <div class="value" style="left:497px"><i></i>DRIVE FOR<br>RESULTS</div>
  <div class="frame"></div>
  <div class="about-photo" role="img" aria-label="Painted pipework and valves at a fuel installation"></div>
</section>

<h2 class="title" style="top:1544px">OUR FOCUS <span>AREA</span></h2>
<p class="lead" style="top:1591px;left:340px;width:520px">Our operations are split into two divisions, Kelvota Inspection Services and Kelvota Engineering services.</p>

<div class="card" style="left:0;top:1696px;width:399px;height:421px;background:linear-gradient(170deg,#6a6c70,#2e2f31)" role="img" aria-label="Pipeline laid in a trench at a storage terminal">
  <span class="num" style="top:336px">01</span>
  <span class="label" style="top:374px">STORAGE TERMINALS</span>
</div>
<div class="card" style="left:799px;top:1696px;width:401px;height:421px;background:linear-gradient(170deg,#6d6c67,#33302c)" role="img" aria-label="Technician checking a valve at a refinery">
  <span class="num" style="top:336px">03</span>
  <span class="label" style="top:374px">REFINERIES</span>
</div>
<div class="card" style="left:399px;top:1667px;width:400px;height:450px;background:linear-gradient(170deg,#1c2a2f,#0c0f12);box-shadow:0 6px 18px rgba(0,0,0,.35)" role="img" aria-label="Ultrasonic testing instrument in use">
  <span class="num" style="top:208px">02</span>
  <span class="label" style="top:246px;left:20px;width:340px">OIL AND GAS OFFSHORE AND ONSHORE RIGS</span>
  <span class="text" style="top:302px">Nemo enim ipsam voluptatem quia voluptas sit aspernatur aut odit aut fugit, sed quia consequuntur magni dolores eos qui ratione voluptatem</span>
  <a class="link" style="left:18px;top:384px">READ MORE</a>
</div>

<section class="how" role="img" aria-label="Welder at work with flying sparks">
  <h2>HOW IT WORKS</h2>
  <svg class="abs" style="left:563px;top:197px" width="74" height="74" viewBox="0 0 74 74"><circle cx="37" cy="37" r="34" fill="none" stroke="#fff" stroke-width="3"/><path d="M29 22 L52 37 L29 52 Z" fill="none" stroke="#fff" stroke-width="3" stroke-linejoin="round"/></svg>
</section>

<h2 class="title" style="top:2633px">LATEST <span>BLOGS</span></h2>
<p class="lead" style="top:2680px;left:330px;width:540px;color:#666">Nemo enim ipsam voluptatem quia voluptas sit aspernatur aut odit aut fugit, sed quia consequuntur magni dolores</p>
<span class="carousel-arrow" style="left:86px">‹</span>
<span class="carousel-arrow" style="left:1094px">›</span>
<div class="blog" style="left:111px;background:linear-gradient(160deg,#8a8a72,#5a3a2c)" role="img" aria-label="Inspector in high visibility vest examining a steel structure">
  <span class="meta" style="top:172px">LOREM IPSUM DOLOR SIT AMET,<br>CONSECTETUR<br>14-02-2020</span>
</div>
<div class="blog" style="left:441px;background:linear-gradient(160deg,#2a2a2e,#5e1c1c);box-shadow:0 6px 16px rgba(0,0,0,.3)" role="img" aria-label="Welder in protective mask working">
  <span class="meta" style="top:92px">LOREM IPSUM DOLOR SIT AMET,<br>CONSECTETUR<br>14-02-2020</span>
  <a class="link" style="left:17px;top:215px;font-size:13px">READ MORE ⊙</a>
</div>
<div class="blog" style="left:770px;background:linear-gradient(160deg,#9aa3ad,#2c3a5a 60%,#b26a4a)" role="img" aria-label="Technician in hard hat inspecting pipes at a tank farm">
  <span class="meta" style="top:172px">LOREM IPSUM DOLOR SIT AMET,<br>CONSECTETUR<br>14-02-2020</span>
</div>

<section class="svc" style="left:0;background:linear-gradient(135deg,var(--red),#9c1016)">
  <h3 style="left:111px">NON DESTRUCTIVE TESTING SERVICES</h3>
  <p style="left:111px">Using the latest ultrasound technology, we can verify the of a material and ascertain the sturdiness of a welded joint. Our technicians are NDT Level II qualified.</p>
  <ul style="left:111px"><li>ULTRASONIC TESTING</li><li>MAGNETIC PARTICLE TESTING</li><li>DYE PENETRANT TESTING</li><li>LEAK TESTING</li><li>VISUAL TESTING</li></ul>
  <a class="btn btn-svc" style="left:114px;background:var(--blue)">READ MORE</a>
</section>
<section class="svc" style="left:600px;background:linear-gradient(135deg,#2a3d86,var(--blue-dark))">
  <h3 style="left:111px">ADVANCED NON DESTRUCTIVE TESTING</h3>
  <p style="left:111px">We are the first local company to introduce this technology. KELVOTA utilises MFL technology to perform corrosion mapping of tank floors.</p>
  <ul style="left:111px"><li>MAGNETIC FLUX LEAKAGE - Tank Bottom inspection</li><li>PHASED ARRAY ULTRASONIC TESTING</li><li>POSITIVE MATERIAL IDENTIFICATION</li><li>3D LASER SCANNING</li><li>MAGNETIC CRAWLER INSPECTION</li></ul>
  <a class="btn btn-svc" style="left:114px;background:var(--red)">READ MORE</a>
</section>
<div class="svc-badge">KELVOTA</div>

<h2 class="title" style="top:3664px">OUR <span>CLIENTS</span></h2>
<div class="client" style="left:111px"><i></i>Halvern Oil</div>
<div class="client" style="left:358px">Corvane Motors</div>
<div class="client" style="left:605px">Brightwell Services</div>
<div class="client" style="left:852px">Inoravo</div>
<div class="dots"><b></b><b></b><b class="on"></b><b></b></div>

<footer class="site-footer">
  <div class="abs" style="left:111px;top:54px;display:flex;align-items:center;gap:10px">
    <span style="width:72px;height:60px;border-radius:50%;background:var(--blue);border:3px solid var(--red);display:block"></span>
    <span class="head" style="font-size:13px;font-weight:600;color:#fff">KELVOTA ENGINEERING</span>
  </div>
  <div class="col" style="left:111px;top:122px;width:280px">We pick the best talent from industry and have heavily investeddeveloping our staff skills further through regular rigorous external and internal training</div>
  <h4 style="left:446px;top:86px">QUICK LINKS</h4>
  <div class="col" style="left:446px;top:122px">Home<br>About Us<br>Inspection<br>Services<br>Blog<br>Contact</div>
  <h4 style="left:606px;top:84px">CONTACT US</h4>
  <div class="col" style="left:606px;top:126px;width:200px">
    <div class="contact-row"><svg width="16" height="16" viewBox="0 0 16 16"><path d="M3 1h3l1.5 4-2 1.2a9 9 0 0 0 4.3 4.3L11 8.5l4 1.5v3a2 2 0 0 1-2 2A12 12 0 0 1 1 3a2 2 0 0 1 2-2z" fill="none" stroke="#ddd" stroke-width="1.2"/></svg><span>254 20 555 0142/3</span></div>
    <div class="contact-row"><svg width="16" height="18" viewBox="0 0 16 18"><path d="M8 1a5.5 5.5 0 0 1 5.5 5.5C13.5 11 8 17 8 17S2.5 11 2.5 6.5A5.5 5.5 0 0 1 8 1z" fill="#ddd"/><circle cx="8" cy="6.5" r="2" fill="#555"/></svg><span>Harbor Road, P.O.<br>BOX 40110-80100<br>Coastline City</span></div>
    <div class="contact-row"><svg width="16" height="14" viewBox="0 0 16 14"><rect x="1" y="2" width="14" height="10" fill="none" stroke="#ddd" stroke-width="1.2"/><path d="M1 2l7 6 7-6" fill="none" stroke="#ddd" stroke-width="1.2"/></svg><span>info@kelvota-eng.com</span></div>
  </div>
  <h4 style="left:840px;top:78px">SUBSCRIBE</h4>
  <div class="email" style="top:115px">Email Address</div>
  <div class="send" style="top:115px"><svg width="20" height="18" viewBox="0 0 20 18"><path d="M1 8L19 1 15 17 9 11z M9 11L19 1" fill="#fff" stroke="#fff" stroke-width="1"/></svg></div>
  <span class="social" style="left:846px;top:195px"></span>
  <span class="social" style="left:879px;top:195px"></span>
  <span class="social" style="left:912px;top:195px"></span>
  <span class="social" style="left:945px;top:195px"></span>
  <div class="footer-rule" style="top:337px"></div>
  <div class="copyright" style="top:365px">© 2020 All Rights Reserved</div>
</footer>

</body>
</html>
```